Design 4 pages for an event discovery website

This is a contest for the design of 4 pages for an events discovery website. The feature is part of the new sign-up process.

Please see the attached document for a full scope, mockups and the parent category icons.

Target Market(s)

18-35 Australian event goers

Industry/Entity Type

Events

Number of Pages Required

4 page

```html
<!DOCTYPE html>
<html lang="en">
<head>
<meta charset="utf-8">
<title>Gathera – Sign Up</title>
<link href="https://fonts.googleapis.com/css2?family=Raleway:wght@300;400;500&family=Open+Sans:wght@400&display=swap" rel="stylesheet">
<style>
  :root {
    --header-top: #3686d2;
    --header-bottom: #1350a7;
    --navy: #0f3f7a;
    --heading-blue: #17407a;
    --orange: #f7941d;
    --text: #333333;
    --footer-bg: #efefef;
    --footer-line: #c9c9c9;
    --social-grey: #6a6a6a;
    --button-blue-top: #4067bf;
    --button-blue-bottom: #36559f;
    --divider: #d4d4d4;
    --white: #ffffff;
  }
  * { box-sizing: border-box; margin: 0; padding: 0; }
  html, body { width: 1200px; height: 570px; overflow: hidden; background: var(--white); }
  body { position: relative; font-family: 'Open Sans', sans-serif; color: var(--text); }

  .site-header {
    position: absolute; left: 0; top: 0; width: 1200px; height: 96px;
    background: linear-gradient(to bottom, var(--header-top), var(--header-bottom));
  }
  .brand {
    position: absolute; left: 141px; top: 18px;
    font-family: 'Raleway', sans-serif; font-weight: 300; font-size: 44px;
    color: var(--white); letter-spacing: -0.5px; line-height: 1; white-space: nowrap;
  }
  .nav-link {
    position: absolute; left: 345px; top: 38px; white-space: nowrap;
    font-family: 'Raleway', sans-serif; font-weight: 400; font-size: 18px; color: var(--white);
  }
  .search-box {
    position: absolute; left: 688px; top: 37px; width: 196px; height: 29px;
    background: var(--white); border: 2px solid #c5cfdb; border-radius: 15px;
    font-size: 10px; color: #555; padding: 7px 0 0 15px;
  }
  .search-box svg { position: absolute; right: 10px; top: 6px; }
  .btn {
    position: absolute; top: 36px; height: 29px; border-radius: 15px;
    font-family: 'Raleway', sans-serif; font-weight: 500; font-size: 13px;
    color: var(--white); text-align: center; line-height: 29px; white-space: nowrap;
  }
  .btn-signup { left: 907px; width: 75px; background: var(--navy); }
  .btn-login { left: 987px; width: 74px; background: var(--orange); }

  .signup-title {
    position: absolute; left: 141px; top: 155px; white-space: nowrap;
    font-family: 'Raleway', sans-serif; font-weight: 300; font-size: 40px; color: var(--heading-blue);
  }
  .connect-button {
    position: absolute; left: 144px; top: 219px; width: 267px; height: 77px;
    background: linear-gradient(to bottom, var(--button-blue-top), var(--button-blue-bottom));
    border-radius: 2px; color: var(--white); font-family: 'Raleway', sans-serif;
  }
  .connect-button .icon-cell {
    position: absolute; left: 0; top: 0; width: 69px; height: 77px;
    border-right: 1px solid #2d4a8c;
  }
  .connect-button .icon-cell span {
    position: absolute; left: 24px; top: 28px; width: 20px; height: 20px;
    background: var(--white); border-radius: 3px;
  }
  .connect-button .lead { position: absolute; left: 93px; top: 15px; font-size: 15px; font-weight: 400; white-space: nowrap; }
  .connect-button .network { position: absolute; left: 93px; top: 29px; font-size: 30px; font-weight: 400; white-space: nowrap; }
  .alt-signup { position: absolute; left: 149px; top: 319px; font-size: 14.5px; color: var(--text); white-space: nowrap; }

  .benefits-title {
    position: absolute; left: 580px; top: 168px; white-space: nowrap;
    font-family: 'Raleway', sans-serif; font-weight: 400; font-size: 23px; color: var(--text);
  }
  .benefit-list { position: absolute; left: 576px; top: 206px; width: 470px; list-style: none; }
  .benefit-list li {
    position: relative; height: 31.6px; padding-left: 32px; line-height: 31.6px;
    font-size: 11.6px; color: var(--text); white-space: nowrap; letter-spacing: -0.05px;
  }
  .benefit-list li + li::before {
    content: ""; position: absolute; left: 0; top: 0; width: 466px; height: 1px;
    background: linear-gradient(to right, var(--divider), var(--divider) 85%, rgba(212,212,212,0));
  }
  .benefit-list svg { position: absolute; left: 4px; top: 7px; }

  .site-footer {
    position: absolute; left: 0; top: 509px; width: 1200px; height: 61px;
    background: var(--footer-bg); border-top: 1px solid var(--footer-line);
  }
  .legal { position: absolute; left: 142px; top: 21px; font-size: 11.5px; color: var(--text); white-space: nowrap; }
  .social-links { position: absolute; left: 975px; top: 20px; display: flex; gap: 5px; }
  .social-links span { width: 19px; height: 19px; background: var(--social-grey); border-radius: 3px; }
</style>
</head>
<body>
  <header class="site-header">
    <div class="brand">Gathera</div>
    <div class="nav-link">Find Events</div>
    <div class="search-box">Search
      <svg width="14" height="14" viewBox="0 0 14 14"><circle cx="5.8" cy="5.8" r="4.3" fill="none" stroke="#8a8a8a" stroke-width="2"/><line x1="9" y1="9" x2="13" y2="13" stroke="#8a8a8a" stroke-width="2.2" stroke-linecap="round"/></svg>
    </div>
    <div class="btn btn-signup">Sign Up</div>
    <div class="btn btn-login">Log In</div>
  </header>

  <main>
    <h1 class="signup-title">Sign Up</h1>
    <div class="connect-button">
      <div class="icon-cell"><span></span></div>
      <div class="lead">Connect with</div>
      <div class="network">Friendnet</div>
    </div>
    <p class="alt-signup">Or Click here to Sign Up without Friendnet</p>

    <h2 class="benefits-title">Feature Benefits</h2>
    <ul class="benefit-list">
      <li><svg width="18" height="18" viewBox="0 0 18 18"><circle cx="9" cy="9" r="9" fill="var(--orange)"/><path d="M4.8 9.2l2.9 2.8 5.6-5.6" fill="none" stroke="#fff" stroke-width="2.2"/></svg>Get personalised event recommendations</li>
      <li><svg width="18" height="18" viewBox="0 0 18 18"><circle cx="9" cy="9" r="9" fill="var(--orange)"/><path d="M4.8 9.2l2.9 2.8 5.6-5.6" fill="none" stroke="#fff" stroke-width="2.2"/></svg>Get notified about your favourite events - never miss out again</li>
      <li><svg width="18" height="18" viewBox="0 0 18 18"><circle cx="9" cy="9" r="9" fill="var(--orange)"/><path d="M4.8 9.2l2.9 2.8 5.6-5.6" fill="none" stroke="#fff" stroke-width="2.2"/></svg>Follow all your favourite artists, musicians, teams and players in one place</li>
      <li><svg width="18" height="18" viewBox="0 0 18 18"><circle cx="9" cy="9" r="9" fill="var(--orange)"/><path d="M4.8 9.2l2.9 2.8 5.6-5.6" fill="none" stroke="#fff" stroke-width="2.2"/></svg>Follow your favourite local venues to know everything happening there</li>
      <li><svg width="18" height="18" viewBox="0 0 18 18"><circle cx="9" cy="9" r="9" fill="var(--orange)"/><path d="M4.8 9.2l2.9 2.8 5.6-5.6" fill="none" stroke="#fff" stroke-width="2.2"/></svg>Get curated news and feature content on your favourite artists (coming soon)</li>
      <li><svg width="18" height="18" viewBox="0 0 18 18"><circle cx="9" cy="9" r="9" fill="var(--orange)"/><path d="M4.8 9.2l2.9 2.8 5.6-5.6" fill="none" stroke="#fff" stroke-width="2.2"/></svg>Invite your mates to events via Friendnet (FN sign-up only)</li>
    </ul>
  </main>

  <footer class="site-footer">
    <div class="legal">© 2015 Company Name&nbsp; All right reserved&nbsp; Term of Use</div>
    <div class="social-links" aria-label="Social links"><span></span><span></span><span></span></div>
  </footer>
</body>
</html>
```